Business Card Design

My business is writing crime novels to entertain readers. I write legal thrillers and mysteries. I need a card for publishers, agents, other authors, and media.

Industry/Entity Type

Legal

Contact Information for Business Card

Paul Derrow
www.derrowfiction.example
pauljderrow@inkpost.example
0064 27 5190472

```html
<!DOCTYPE html>
<html lang="en">
<head>
<meta charset="utf-8">
<title>Paul Derrow – Business Card</title>
<link href="https://fonts.googleapis.com/css2?family=Delius&family=Gochi+Hand&display=swap" rel="stylesheet">
<style>
  :root {
    --page-bg: #e9e4d8;
    --card-black: #050505;
    --card-shadow: rgba(0, 0, 0, 0.35);
    --accent-red: #d8000a;
    --accent-red-dark: #7a0005;
    --accent-red-light: #ff2a2a;
    --smoke-red: #5a0a0e;
    --text-white: #ffffff;
    --photo-dark: #1d1d1d;
    --photo-mid: #6b5a52;
  }
  * { box-sizing: border-box; margin: 0; padding: 0; }
  html, body {
    width: 1200px;
    height: 729px;
    overflow: hidden;
    background: var(--page-bg);
  }
  .canvas {
    position: relative;
    width: 1200px;
    height: 729px;
    display: flex;
    align-items: center;
    justify-content: center;
  }
  .business-card {
    position: relative;
    width: 900px;
    height: 500px;
    border-radius: 34px;
    background: var(--card-black);
    overflow: hidden;
    box-shadow: 0 14px 30px var(--card-shadow);
  }
  .smoke-decoration {
    position: absolute;
    top: 30px;
    right: 40px;
    width: 430px;
    height: 230px;
    border-radius: 50%;
    background: radial-gradient(ellipse at center, var(--smoke-red) 0%, rgba(90, 10, 14, 0.45) 40%, rgba(0, 0, 0, 0) 72%);
  }
  .portrait {
    position: absolute;
    left: 70px;
    bottom: 0;
    width: 380px;
    height: 410px;
    border-radius: 180px 180px 0 0;
    background: linear-gradient(180deg, var(--photo-mid) 0%, #4a3e39 35%, var(--photo-dark) 70%, #111 100%);
  }
  .name-band {
    position: absolute;
    left: 440px;
    right: 0;
    bottom: 0;
    height: 118px;
    background: linear-gradient(180deg, var(--accent-red-light) 0%, var(--accent-red) 45%, var(--accent-red-dark) 100%);
    display: flex;
    align-items: center;
    justify-content: center;
  }
  .card-name {
    font-family: "Gochi Hand", cursive;
    font-size: 64px;
    letter-spacing: 2px;
    color: var(--text-white);
  }
  .contact-list {
    position: absolute;
    left: 480px;
    top: 220px;
    list-style: none;
    display: flex;
    flex-direction: column;
    gap: 14px;
  }
  .contact-item {
    display: flex;
    align-items: center;
    gap: 14px;
    font-family: "Delius", cursive;
    font-size: 24px;
    color: var(--text-white);
  }
  .contact-icon {
    width: 22px;
    height: 22px;
    flex: none;
    fill: var(--accent-red);
  }
</style>
</head>
<body>
<main class="canvas">
  <article class="business-card">
    <div class="smoke-decoration" role="img" aria-label="Faint red smoke swirl decoration"></div>
    <div class="portrait" role="img" aria-label="Portrait photograph of the author in a dark leather jacket"></div>

    <ul class="contact-list">
      <li class="contact-item">
        <svg class="contact-icon" viewBox="0 0 24 24" aria-hidden="true">
          <path d="M3 7c0-2 2-3 9-3s9 1 9 3v2h-5V7.5c-1-.5-7-.5-8 0V9H3z"/>
          <path d="M6 11l3-2h6l3 2 2 8H4z"/>
        </svg>
        <span>0064 27 5190472</span>
      </li>
      <li class="contact-item">
        <svg class="contact-icon" viewBox="0 0 24 24" aria-hidden="true">
          <path d="M2 6h20v12H2z"/>
          <path d="M2 6l10 7 10-7" fill="none" stroke="#050505" stroke-width="1.6"/>
        </svg>
        <span>pauljderrow@inkpost.example</span>
      </li>
      <li class="contact-item">
        <svg class="contact-icon" viewBox="0 0 24 24" aria-hidden="true">
          <circle cx="12" cy="12" r="10"/>
          <g fill="none" stroke="#050505" stroke-width="1.4">
            <ellipse cx="12" cy="12" rx="4.5" ry="10"/>
            <path d="M2 12h20M4 7h16M4 17h16"/>
          </g>
        </svg>
        <span>www.derrowfiction.example</span>
      </li>
    </ul>

    <div class="name-band">
      <h1 class="card-name">Paul Derrow</h1>
    </div>
  </article>
</main>
</body>
</html>
```